Behavioral Health Booth Backdrop Design

I need a design created for our backdrop as we are purchasing a new curved 10x10 backdrop for our trade shows. We are a behavioral health (mental health and addiction services) agency and want something that catches your eye when walking by. We don't want a lot of "words" or description on it, but more of a catchy look. I have attached some pics that we like the colors of in general (abstract). This doesn't mean that you need to use these specific pics. I have also attached our Logo with our name.

Requirements
Must have
• Eye catchy design and or a picture/photo with our agency name and/or logo on the backdrop. One of the files to be a vector file.

```html
<!DOCTYPE html>
<html lang="en">
<head>
<meta charset="utf-8">
<title>Alder Vale Behavioral Health Solutions – Booth Backdrop</title>
<link rel="stylesheet" href="https://fonts.googleapis.com/css2?family=Bebas+Neue&family=Lobster&display=swap">
<style>
  :root {
    --canvas-grey: #dedfdf;
    --panel-white: #ffffff;
    --frame-line: #8a8a8a;
    --ink-purple: #47378c;
    --ink-pink: #e2265f;
    --ink-charcoal: #2f2f33;
    --mark-green: #5b9a3c;
    --wash-indigo: #3b2fa6;
    --wash-magenta: #e0245e;
    --wash-yellow: #f4e22a;
    --wash-green: #7cbd3a;
    --wash-teal: #2f9c8c;
  }
  * { margin: 0; padding: 0; box-sizing: border-box; }
  html, body {
    width: 1192px;
    height: 1200px;
    overflow: hidden;
    background: var(--canvas-grey);
  }
  .backdrop {
    position: absolute;
    left: 45px;
    top: 48px;
    width: 1102px;
    height: 1102px;
    background: var(--panel-white);
    border: 1px solid var(--frame-line);
    overflow: hidden;
  }
  .watercolor-art {
    position: absolute;
    left: 0;
    top: 0;
    width: 100%;
    height: 780px;
    background:
      linear-gradient(180deg, rgba(255,255,255,0) 0%, rgba(255,255,255,0) 45%, rgba(255,255,255,0.85) 72%, #ffffff 100%),
      linear-gradient(135deg, var(--wash-indigo) 0%, var(--wash-magenta) 30%, var(--wash-yellow) 55%, var(--wash-green) 78%, var(--wash-teal) 100%);
  }
  .brand {
    position: absolute;
    left: 266px;
    top: 592px;
    display: flex;
    align-items: center;
    gap: 24px;
  }
  .brand-dot {
    width: 104px;
    height: 104px;
    border-radius: 50%;
    background: var(--mark-green);
    flex: none;
  }
  .brand-name {
    font-family: "Bebas Neue", sans-serif;
    color: var(--ink-charcoal);
    line-height: 0.95;
  }
  .brand-name .brand-line-main { display: block; font-size: 68px; letter-spacing: 6px; }
  .brand-name .brand-line-sub { display: block; font-size: 32px; letter-spacing: 3px; }
  .headline {
    position: absolute;
    left: 0;
    top: 786px;
    width: 100%;
    text-align: center;
    font-family: "Bebas Neue", sans-serif;
    font-weight: 400;
    font-size: 74px;
    line-height: 80px;
    color: var(--ink-purple);
    letter-spacing: 0.5px;
  }
  .headline .accent { color: var(--ink-pink); }
  .tagline {
    position: absolute;
    left: 0;
    top: 940px;
    width: 100%;
    text-align: center;
    font-family: "Lobster", cursive;
    font-size: 52px;
    line-height: 64px;
    color: var(--ink-purple);
  }
</style>
</head>
<body>
  <main class="backdrop">
    <div class="watercolor-art" role="img" aria-label="Abstract watercolor artwork in indigo, magenta, yellow and green washes"></div>

    <div class="brand">
      <span class="brand-dot"></span>
      <span class="brand-name">
        <span class="brand-line-main">Alder Vale</span>
        <span class="brand-line-sub">Behavioral Health Solutions</span>
      </span>
    </div>

    <h1 class="headline">
      Comprehensive <span class="accent">Mental Health</span><br>
      and <span class="accent">Addiction</span> Services.
    </h1>
    <p class="tagline">Where hope begins.</p>
  </main>
</body>
</html>
```